Website Redesign for Existing BBQ Catering Company

Need to get my website (HollowOakSmoke.com) redesigned. Looking for a cleaner look but still patriotic and rustic. Would like to add parallax scrolling on the menu page and include some pics from our photo gallery. Would like to display a picture of the brisket before scrolling into the meat section of our menu and the same for the other sections too.....picture of one of our sides, appetizers, desserts, etc.

Would also like to add three new pages called Corporate Events, Weddings, and Veteran Events possibly in a drop-down menu called Catering. You can use pics from our Facebook page. We've posted tons of pics from weddings that we've done. I've uploaded some corporate and wedding pics but you can pics the ones that look best. I can swap them out later if needed.

Would like to keep it Wordpress if possible so I can update it as needed.

Also need to add some links to our storefront on The Vow Loft. I have the HTML code and will upload the image here.

Also need to add social media links for our Facebook, Instagram and Twitter pages.

The contact form that I'm using now feeds the leads into another site called Tenbrim.com that I use to manage my clients.

Target Market(s)

Weddings, corporate events, veterans

Industry/Entity Type

Catering

Coding

Coded - Design and coding required

Number of Pages Required

5+ page

Colors
ec1f27
3176b5
ffffff

Requirements
Must have
• Really like the hero image design. Looks less like a template. Check out https://lumarenne.com and https://corvellagrille.com
• Would like to keep somewhat of a rustic and patriotic look and feel like the site currently is. We mainly cater in barn weddings and we cater for a lot of veterans. Will be pushing more corporate catering next year and opening a restaurant.

```html
<!DOCTYPE html>
<html lang="en">
<head>
<meta charset="utf-8">
<title>Hollow Oak Smoke</title>
<link rel="stylesheet" href="https://fonts.googleapis.com/css2?family=Great+Vibes&family=Lobster&family=Oswald:wght@300&family=Jost:wght@400;500&display=swap">
<style>
:root{
  --red:#ec1f27;
  --blue:#3176b5;
  --white:#ffffff;
  --bark-dark:#4a3c1e;
  --bark-mid:#7a6a3c;
  --bark-light:#9c8a55;
  --badge:#8cc3e6;
  --tile:#f1f1f3;
}
*{margin:0;padding:0;box-sizing:border-box}
html,body{width:862px;height:1200px;overflow:hidden}
body{
  position:relative;
  font-family:'Jost',sans-serif;
  background:
    radial-gradient(ellipse at 30% 20%,rgba(180,160,100,.35),transparent 60%),
    radial-gradient(ellipse at 80% 70%,rgba(60,45,20,.45),transparent 60%),
    linear-gradient(135deg,var(--bark-mid),var(--bark-dark) 45%,var(--bark-light) 75%,var(--bark-dark));
}
.brand{
  position:absolute;left:48px;top:22px;width:122px;height:122px;border-radius:50%;
  background:var(--red);border:5px solid var(--white);z-index:3;
  display:flex;align-items:center;justify-content:center;text-align:center;
  color:var(--white);font-family:'Jost',sans-serif;font-weight:500;font-size:14px;line-height:1.2;padding:12px;
}
.call{position:absolute;top:18px;right:70px;display:flex;align-items:baseline;gap:10px}
.call-label{font-family:'Lobster',cursive;color:var(--red);font-size:24px}
.call-phone{font-family:'Oswald',sans-serif;font-weight:300;color:var(--white);font-size:26px}
.main-nav{position:absolute;top:69px;left:240px;width:552px;display:flex;justify-content:space-between;font-size:11.5px;font-weight:500;color:var(--white)}
.main-nav .active{color:var(--red)}
.hero{
  position:absolute;left:71px;top:102px;width:720px;height:346px;
  background:
    radial-gradient(ellipse at 60% 60%,rgba(190,80,50,.7),transparent 55%),
    linear-gradient(160deg,#4a3a33 0%,#6e3a28 35%,#3a2418 60%,#8a5a40 100%);
  box-shadow:0 4px 12px rgba(0,0,0,.4);
}
.hero-title{position:absolute;top:108px;width:100%;text-align:center;font-family:'Great Vibes',cursive;color:var(--white);font-size:62px;line-height:1.2;text-shadow:0 2px 6px rgba(0,0,0,.4)}
.hero-dots{position:absolute;top:304px;left:333px;display:flex;gap:3px}
.hero-dots span{width:12px;height:12px;border-radius:50%;background:var(--white)}
.hero-dots span:first-child{background:transparent;border:2px solid var(--white)}
.welcome{position:absolute;left:71px;top:448px;width:720px;height:254px;background:var(--blue);color:var(--white);text-align:center;padding:32px 52px 0}
.welcome h1{font-family:'Great Vibes',cursive;font-weight:400;font-size:38px;margin-bottom:14px}
.welcome p{font-size:9.4px;line-height:19px;margin-bottom:16px}
.features{
  position:absolute;left:71px;top:702px;width:720px;height:350px;
  background-color:var(--tile);
  background-image:radial-gradient(circle,rgba(0,0,0,.05) 1px,transparent 1.5px);
  background-size:8px 8px;
}
.card{position:absolute;top:34px;width:190px;height:260px;background:var(--blue);box-shadow:0 2px 6px rgba(0,0,0,.25);text-align:center;color:var(--white)}
.card-photo{height:132px;border-radius:40px 40px 0 0;border:2px solid var(--blue);margin-top:-2px}
.card h2{font-family:'Great Vibes',cursive;font-weight:400;font-size:28px;margin:8px 0 4px}
.card p{font-size:8px;line-height:12.5px;padding:0 16px;height:40px}
.btn{display:inline-block;margin-top:9px;background:var(--red);color:var(--white);font-size:7.5px;border-radius:8px;padding:3px 13px}
.badge{position:absolute;left:397px;top:1009px;width:70px;height:70px;border-radius:50%;background:var(--badge);border:2px solid var(--white);z-index:2}
.footer{position:absolute;left:71px;top:1052px;width:720px;height:92px;background:var(--red);color:var(--white)}
.footer svg.edge{position:absolute;top:-6px;left:0}
.footer-nav{position:absolute;top:33px;width:100%;display:flex;justify-content:center;gap:9px;font-size:7.5px;color:rgba(255,255,255,.75)}
.copyright{position:absolute;top:63px;left:23px;font-size:9.5px}
.social{position:absolute;top:66px;left:667px;display:flex;gap:6px}
.social span{width:8px;height:8px;border-radius:50%;background:var(--white)}
</style>
</head>
<body>
<div class="brand">Hollow Oak Smoke BBQ</div>
<div class="call"><span class="call-label">Call Us Today ! ! !</span><span class="call-phone">555-014-2736</span></div>
<nav class="main-nav">
  <span class="active">Home</span><span>Menu</span><span>Photo Gallery</span><span>Corporate Catering</span><span>Weddings</span><span>Veteran Events</span><span>Contact</span>
</nav>

<section class="hero" role="img" aria-label="Close-up of smoked brisket being sliced with a knife">
  <div class="hero-title">Hollow Oak Smoke</div>
  <div class="hero-dots"><span></span><span></span><span></span><span></span></div>
</section>

<section class="welcome">
  <h1>Welcome to Hollow Oak Smoke</h1>
  <p>Sed ut perspiciatis unde omnis iste natus error sit voluptatem accusantium doloremque laudantium, totam rem aperiam, eaque ipsa quae ab illo inventore veritatis et quasi architecto beatae vitae dicta sunt explicabo. Nemo enim ipsam voluptatem quia voluptas sit aspernatur aut odit aut fugit, sed quia consequuntur magni dolores eos qui ratione voluptatem sequi nesciunt.</p>
  <p>But I must explain to you how all this mistaken idea of denouncing pleasure and praising pain was born and I will give you a complete account of the system, and expound the actual teachings of the great explorer of the truth, the master-builder of human happiness.</p>
</section>

<section class="features">
  <article class="card" style="left:31px">
    <div class="card-photo" role="img" aria-label="Catering staff serving food at an outdoor buffet" style="background:linear-gradient(180deg,#7fa0c4,#8a6a6a 45%,#2a2a2a)"></div>
    <h2>About Us</h2>
    <p>Hollow Oak Smoke is a BBQ Catering Company opened with a mission to give back to the veteran community.</p>
    <span class="btn">Read more</span>
  </article>
  <article class="card" style="left:265px">
    <div class="card-photo" role="img" aria-label="Berry pie with a flag-style lattice crust" style="background:linear-gradient(180deg,#c9a070,#3a3050 50%,#d6b58a)"></div>
    <h2>Our Menu</h2>
    <p>Hollow Oak Smoke is committed to serving amazing BBQ. We don't take shortcuts and put a lot of love into our BBQ that we guarantee..</p>
    <span class="btn">Read more</span>
  </article>
  <article class="card" style="left:499px">
    <div class="card-photo" role="img" aria-label="BBQ smoker trailer parked outside a building" style="background:linear-gradient(180deg,#5d9ad8,#d8d4cc 50%,#555)"></div>
    <h2>Contact Us</h2>
    <p>Feel free to contact us with any questions you might have. We'd love to hear from ya.</p>
    <span class="btn">Read more</span>
  </article>
</section>

<div class="badge" role="img" aria-label="The Vow Loft listing badge"></div>

<footer class="footer">
  <svg class="edge" width="720" height="7" viewBox="0 0 720 7" preserveAspectRatio="none" aria-hidden="true">
    <defs><pattern id="zig" width="6" height="7" patternUnits="userSpaceOnUse"><path d="M0 7 L3 0 L6 7 Z" fill="#ec1f27"/></pattern></defs>
    <rect width="720" height="7" fill="url(#zig)"/>
  </svg>
  <nav class="footer-nav">
    <span>Home</span><span>|</span><span>Menu</span><span>|</span><span>Photo Gallery</span><span>|</span><span>Corporate Catering</span><span>|</span><span>Weddings</span><span>|</span><span>Veteran Events</span><span>|</span><span>Contact</span>
  </nav>
  <p class="copyright">Copyright 2017 © Hollow Oak Smoke. All rights reserved.</p>
  <div class="social" aria-label="Social links"><span></span><span></span><span></span></div>
</footer>
</body>
</html>
```